Brainwave state designs for neurofeedback report

Design ORIGINAL graphics that correspond with existing colors and shapes for Halo Prism Grid of Stillness & Halo Prism Rhythm Panel for "Normal", "Bright Harbor", "Summit Tide" etc... patterns. You can change the shape of the white outline to be more modern looking. Perhaps you can also use white background with black outline. The frequency bars (can be more ordered) but keep the general shape of the outline.

• An original flair. Modern. Neurotechish
• Do not copy the design. Add your original ideas. Choose a font that complements the design.

```html
<!DOCTYPE html>
<html lang="en">
<head>
<meta charset="utf-8">
<title>Brainwave State Chart</title>
<link rel="stylesheet" href="https://fonts.googleapis.com/css2?family=Montserrat:wght@400;600&display=swap">
<style>
  :root {
    --page: #ffffff;
    --ink: #111111;
    --outline: #1c1f26;
    --outline-glow: #c1272d;
    --divider: #c1272d;
    --grid: #e9ecf1;
    --axis-bar: #2e7d3a;
    --beta: #f26a36;
    --alpha: #3a8a3f;
    --theta: #5b8fd0;
    --delta: #932c8f;
    --ice-top: #3c434b;
    --ice-sky: #5a626b;
    --ice-water: #d6dce1;
    --ice-mid: #2a3138;
    --ice-low: #0b0d10;
  }
  html, body {
    margin: 0;
    padding: 0;
    width: 1200px;
    height: 928px;
    overflow: hidden;
    background: var(--page);
  }
  .brainwave-chart {
    display: block;
    width: 1200px;
    height: 928px;
    font-family: "Montserrat", sans-serif;
  }
  .freq-label { font-size: 22px; fill: var(--ink); text-anchor: middle; font-weight: 400; }
  .axis-label { font-size: 22px; fill: var(--ink); text-anchor: middle; font-weight: 400; }
  .state-label { font-size: 23px; font-weight: 600; text-anchor: middle; }
  .state-beta { fill: var(--beta); }
  .state-alpha { fill: var(--alpha); }
  .state-theta { fill: var(--theta); }
  .state-delta { fill: var(--delta); }
  .grid-line { stroke: var(--grid); stroke-width: 1.5; }
  .wave-glow { fill: none; stroke: var(--outline-glow); stroke-opacity: 0.18; stroke-width: 12; stroke-linejoin: round; stroke-linecap: round; }
  .wave-outline { fill: none; stroke: var(--outline); stroke-width: 3.5; stroke-linejoin: round; stroke-linecap: round; }
  .wave-node { fill: var(--page); stroke: var(--outline); stroke-width: 2.5; }
  .band-divider { stroke: var(--divider); stroke-width: 2.5; stroke-dasharray: 10 7; }
  .axis-bar { fill: var(--axis-bar); }
  .axis-tick { stroke: var(--page); stroke-width: 3; }
</style>
</head>
<body>
<svg class="brainwave-chart" viewBox="0 0 1584 1224" xmlns="http://www.w3.org/2000/svg">
  <defs>
    <linearGradient id="iceberg-tone" x1="0" y1="0" x2="0" y2="1">
      <stop offset="0" stop-color="var(--ice-top)"/>
      <stop offset="0.28" stop-color="var(--ice-sky)"/>
      <stop offset="0.31" stop-color="#9aa3ab"/>
      <stop offset="0.37" stop-color="var(--ice-water)"/>
      <stop offset="0.44" stop-color="#7d8790"/>
      <stop offset="0.47" stop-color="var(--ice-mid)"/>
      <stop offset="1" stop-color="var(--ice-low)"/>
    </linearGradient>
  </defs>

  <g class="iceberg-illustration" role="img" aria-label="Iceberg floating in dark water, small peak above the surface and a large mass below">
    <rect x="1001" y="287" width="514" height="651" fill="url(#iceberg-tone)"/>
  </g>

  <g class="amplitude-grid">
    <line class="grid-line" x1="332" y1="296" x2="332" y2="816"/>
    <line class="grid-line" x1="268" y1="296" x2="268" y2="816"/>
    <line class="grid-line" x1="208" y1="296" x2="208" y2="816"/>
    <line class="grid-line" x1="144" y1="296" x2="144" y2="816"/>
    <line class="grid-line" x1="550" y1="296" x2="550" y2="816"/>
    <line class="grid-line" x1="614" y1="296" x2="614" y2="816"/>
    <line class="grid-line" x1="678" y1="296" x2="678" y2="816"/>
    <line class="grid-line" x1="742" y1="296" x2="742" y2="816"/>
  </g>

  <g class="frequency-bars-left">
    <rect x="343" y="306" width="52" height="26" rx="13" fill="#f04e35"/>
    <rect x="351" y="343" width="44" height="26" rx="13" fill="#f15a35"/>
    <rect x="320" y="380" width="75" height="26" rx="13" fill="#f5793a"/>
    <rect x="291" y="416" width="104" height="26" rx="13" fill="#f68b3a"/>
    <rect x="283" y="453" width="112" height="26" rx="13" fill="#f9a53b"/>
    <rect x="282" y="490" width="113" height="26" rx="13" fill="#5a9250"/>
    <rect x="193" y="527" width="202" height="26" rx="13" fill="#3a8a3f"/>
    <rect x="225" y="563" width="170" height="26" rx="13" fill="#1f6b33"/>
    <rect x="312" y="600" width="83" height="26" rx="13" fill="#5b9bd5"/>
    <rect x="288" y="637" width="107" height="26" rx="13" fill="#5b97d3"/>
    <rect x="321" y="673" width="74" height="26" rx="13" fill="#6e7dbe"/>
    <rect x="251" y="710" width="144" height="26" rx="13" fill="#7e61ad"/>
    <rect x="273" y="747" width="122" height="26" rx="13" fill="#8e4c9e"/>
    <rect x="357" y="783" width="38" height="26" rx="13" fill="#9c3e93"/>
  </g>

  <g class="frequency-bars-right">
    <rect x="487" y="306" width="69" height="26" rx="13" fill="#f04e35"/>
    <rect x="487" y="343" width="50" height="26" rx="13" fill="#f15a35"/>
    <rect x="487" y="380" width="69" height="26" rx="13" fill="#f5793a"/>
    <rect x="487" y="416" width="75" height="26" rx="13" fill="#f68b3a"/>
    <rect x="487" y="453" width="95" height="26" rx="13" fill="#f9a53b"/>
    <rect x="487" y="490" width="117" height="26" rx="13" fill="#5a9250"/>
    <rect x="487" y="527" width="230" height="26" rx="13" fill="#3a8a3f"/>
    <rect x="487" y="563" width="230" height="26" rx="13" fill="#1f6b33"/>
    <rect x="487" y="600" width="69" height="26" rx="13" fill="#5b9bd5"/>
    <rect x="487" y="637" width="123" height="26" rx="13" fill="#5b97d3"/>
    <rect x="487" y="673" width="87" height="26" rx="13" fill="#6e7dbe"/>
    <rect x="487" y="710" width="123" height="26" rx="13" fill="#7e61ad"/>
    <rect x="487" y="747" width="99" height="26" rx="13" fill="#8e4c9e"/>
    <rect x="487" y="783" width="34" height="26" rx="13" fill="#9c3e93"/>
  </g>

  <g class="frequency-labels">
    <text class="freq-label" x="442" y="327">38</text>
    <text class="freq-label" x="442" y="364">30</text>
    <text class="freq-label" x="442" y="401">24</text>
    <text class="freq-label" x="442" y="437">19</text>
    <text class="freq-label" x="442" y="474">15</text>
    <text class="freq-label" x="442" y="511">12.5</text>
    <text class="freq-label" x="442" y="548">10.5</text>
    <text class="freq-label" x="442" y="584">9</text>
    <text class="freq-label" x="442" y="621">7.5</text>
    <text class="freq-label" x="442" y="658">6</text>
    <text class="freq-label" x="442" y="694">4</text>
    <text class="freq-label" x="442" y="731">3</text>
    <text class="freq-label" x="442" y="768">1.5</text>
    <text class="freq-label" x="442" y="804">0.75</text>
  </g>

  <g class="wave-envelope">
    <polyline class="wave-glow" points="342,293 328,321 338,345 316,382 280,428 268,468 265,503 175,540 205,576 298,613 265,650 304,686 234,723 258,760 343,798"/>
    <polyline class="wave-glow" points="562,295 576,321 555,353 570,390 575,428 620,503 734,540 733,576 578,612 632,650 592,686 634,723 608,762 548,797"/>
    <polyline class="wave-outline" points="342,293 328,321 338,345 316,382 280,428 268,468 265,503 175,540 205,576 298,613 265,650 304,686 234,723 258,760 343,798"/>
    <polyline class="wave-outline" points="562,295 576,321 555,353 570,390 575,428 620,503 734,540 733,576 578,612 632,650 592,686 634,723 608,762 548,797"/>
    <circle class="wave-node" cx="175" cy="540" r="5"/>
    <circle class="wave-node" cx="298" cy="613" r="5"/>
    <circle class="wave-node" cx="265" cy="650" r="5"/>
    <circle class="wave-node" cx="234" cy="723" r="5"/>
    <circle class="wave-node" cx="734" cy="540" r="5"/>
    <circle class="wave-node" cx="632" cy="650" r="5"/>
    <circle class="wave-node" cx="634" cy="723" r="5"/>
  </g>

  <g class="band-dividers">
    <line class="band-divider" x1="78" y1="484" x2="1240" y2="484"/>
    <line class="band-divider" x1="78" y1="595" x2="1240" y2="595"/>
    <line class="band-divider" x1="78" y1="704" x2="1240" y2="704"/>
  </g>

  <g class="state-labels">
    <text class="state-label state-beta" x="822" y="384">Beta</text>
    <text class="state-label state-beta" x="822" y="413">Conscious Mind</text>
    <text class="state-label state-alpha" x="822" y="532">Alpha</text>
    <text class="state-label state-alpha" x="822" y="560">Bridge</text>
    <text class="state-label state-theta" x="822" y="650">Theta</text>
    <text class="state-label state-theta" x="822" y="678">Conscious Mind</text>
    <text class="state-label state-delta" x="822" y="760">Delta</text>
    <text class="state-label state-delta" x="822" y="788">Conscious Mind</text>
  </g>

  <g class="amplitude-axis">
    <text class="axis-label" x="82" y="861">15</text>
    <text class="axis-label" x="144" y="861">12</text>
    <text class="axis-label" x="208" y="861">9</text>
    <text class="axis-label" x="268" y="861">6</text>
    <text class="axis-label" x="332" y="861">3</text>
    <text class="axis-label" x="550" y="861">3</text>
    <text class="axis-label" x="614" y="861">6</text>
    <text class="axis-label" x="678" y="861">9</text>
    <text class="axis-label" x="742" y="861">12</text>
    <text class="axis-label" x="806" y="861">15</text>
    <rect class="axis-bar" x="61" y="879" width="334" height="29" rx="14.5"/>
    <rect class="axis-bar" x="487" y="879" width="335" height="29" rx="14.5"/>
    <line class="axis-tick" x1="144" y1="883" x2="144" y2="904"/>
    <line class="axis-tick" x1="208" y1="883" x2="208" y2="904"/>
    <line class="axis-tick" x1="268" y1="883" x2="268" y2="904"/>
    <line class="axis-tick" x1="332" y1="883" x2="332" y2="904"/>
    <line class="axis-tick" x1="550" y1="883" x2="550" y2="904"/>
    <line class="axis-tick" x1="614" y1="883" x2="614" y2="904"/>
    <line class="axis-tick" x1="678" y1="883" x2="678" y2="904"/>
    <line class="axis-tick" x1="742" y1="883" x2="742" y2="904"/>
  </g>
</svg>
</body>
</html>
```